Kesso Tea Premium Matcha brand Label

This is a label design project for a luxury tea brand. Feel free to be creative within the guidelines.
Attached to this project is a document called “Private Label Design Requirements” with the design guidelines and template. There is another document called "Kesso Tea Packaging Instructions" this has more details necessary to stick to the guidelines in the first document.

I have also attached the certifications to be included as well as different variations of the logo for you to use.

If you have any questions, I am here.
Updates

Need extra days to review

Target Market(s)

Young, active, fun, enjoy the finer things

```html
<!DOCTYPE html>
<html lang="en">
<head>
<meta charset="utf-8">
<title>Kesso Tea Premium Ceremonial Matcha Label</title>
<link href="https://fonts.googleapis.com/css2?family=Marcellus&family=Oswald:wght@300;400&family=Montserrat:wght@500;600;700&display=swap" rel="stylesheet">
<style>
  :root {
    --backdrop: #8e8f93;
    --matcha-green: #6cbf4a;
    --ink-black: #0b0b0b;
    --paper-white: #ffffff;
    --paper-shade: #e6e7e8;
    --text-dark: #111111;
  }
  * { margin: 0; padding: 0; box-sizing: border-box; }
  html, body { width: 1200px; height: 620px; overflow: hidden; }
  body { background: var(--backdrop); position: relative; font-family: "Montserrat", sans-serif; }

  .label {
    position: absolute; left: 40px; top: 200px;
    width: 1120px; height: 219px;
    box-shadow: 0 3px 8px rgba(0,0,0,0.3);
    overflow: hidden;
  }
  .label-art { position: absolute; inset: 0; width: 100%; height: 100%; }

  .brand {
    position: absolute; left: 458px; top: 262px;
    display: flex; align-items: center; gap: 6px;
    font-family: "Marcellus", serif; font-size: 16px; color: var(--matcha-green);
  }
  .brand-dot { width: 12px; height: 12px; border-radius: 50%; background: var(--matcha-green); }

  .title { position: absolute; left: 563px; top: 245px; color: var(--paper-white); font-family: "Marcellus", serif; }
  .title-line { font-size: 23px; line-height: 24px; display: block; }
  .title-rule { width: 133px; height: 1.5px; background: var(--matcha-green); margin: 3px 0 1px; }
  .title-product { font-family: "Oswald", sans-serif; font-weight: 300; font-size: 33px; line-height: 36px; color: var(--matcha-green); letter-spacing: 0.5px; }

  .net-weight { position: absolute; left: 560px; top: 376px; width: 80px; text-align: center; font-family: "Marcellus", serif; font-size: 11px; color: var(--text-dark); }

  .origin { position: absolute; left: 121px; top: 289px; font-size: 9.5px; font-weight: 600; line-height: 12px; color: var(--text-dark); }
  .origin .cert { margin-top: 6px; }

  .details { position: absolute; left: 906px; top: 256px; color: var(--text-dark); }
  .details h3 { font-size: 11.5px; font-weight: 700; line-height: 13px; }
  .details p, .details li { font-size: 7.5px; font-weight: 600; line-height: 9.5px; }
  .details ul { list-style: none; margin-bottom: 5px; }
  .details li::before { content: "\2022 "; }
  .details .ingredients { margin-bottom: 4px; }
  .certs { display: flex; align-items: center; gap: 6px; margin-top: 2px; }
  .badge-square { width: 24px; height: 26px; background: var(--matcha-green); border-radius: 2px; }
  .badge-round { width: 26px; height: 26px; border-radius: 50%; background: var(--paper-white); border: 3px solid #1f7a3a; }
  .storage { font-size: 7.5px; font-weight: 700; line-height: 9px; margin-left: 4px; }
</style>
</head>
<body>
  <section class="label">
    <svg class="label-art" viewBox="0 0 1482 290" preserveAspectRatio="none" aria-hidden="true">
      <defs>
        <linearGradient id="paper" x1="0" y1="0" x2="1" y2="1">
          <stop offset="0" stop-color="var(--paper-shade)"/>
          <stop offset="0.5" stop-color="#ffffff"/>
          <stop offset="1" stop-color="var(--paper-shade)"/>
        </linearGradient>
      </defs>
      <rect width="1482" height="290" fill="url(#paper)"/>
      <path d="M0,0 H1160 C1090,150 980,255 830,290 H0 Z" fill="var(--matcha-green)"/>
      <path d="M340,0 C400,150 520,260 660,290" fill="none" stroke="#ffffff" stroke-width="5"/>
      <path d="M1148,0 C1080,140 980,235 830,262" fill="none" stroke="#ffffff" stroke-width="4"/>
      <path d="M360,0 H1140 C1060,150 920,226 740,222 C560,218 430,130 360,0 Z" fill="var(--ink-black)"/>
      <path d="M372,10 C450,150 580,232 750,236 C900,238 1010,190 1080,120" fill="none" stroke="#ffffff" stroke-width="3"/>
    </svg>
  </section>

  <div class="brand"><span class="brand-dot"></span>Kesso Tea</div>

  <div class="title">
    <span class="title-line">Premium Organic</span>
    <span class="title-line">Ceremonial</span>
    <div class="title-rule"></div>
    <span class="title-product">MATCHA</span>
  </div>

  <div class="net-weight">Net Wt: 30g</div>

  <div class="origin">
    <p>Product of Japan</p>
    <p>Distributed by:</p>
    <p>Kesso Tea Co. | Riverton, Ga</p>
    <p class="cert">Certified Organic by nora</p>
  </div>

  <div class="details">
    <h3>Ingredients:</h3>
    <p class="ingredients">Premium Organic Japanese Matcha Green Tea</p>
    <h3>Instructions:</h3>
    <ul>
      <li>2 tsp of Matcha</li>
      <li>2oz of Water (170-180 degrees F)</li>
      <li>Whisk in a W formation until frothy</li>
      <li>Sweeten to taste</li>
    </ul>
    <div class="certs">
      <span class="badge-square"></span>
      <span class="badge-round"></span>
      <p class="storage">KEEP REFRIGERATED<br>FOR QUALITY</p>
    </div>
  </div>
</body>
</html>
```